Homepage for the brisk-find Web Application

At the end of this text, you will find a link to a website that is under construction for a webApp that I intend to launch soon. The contest goal is for you to make redesign the homepage in a nice, fresh, modern Style. Only design, no coding necessary. It needs to have a responsive version for small screens like smart phones. Attached is the text for it, and some images that you may use. You are welcome to find or create additional supporting images. You can use PixTrove.example or similar service to find new images as long as I can purchase the non-exclusive use rights for the images at similar prices. The contest is just for the home page. However, the winner, if I like the work and we can agree on a fair price, could be contracted on a one-on-one basis to do the rest of the site. You are welcome to suggest minor changes like font sizes and minor variations on the Header banner, but that banner is consistent with the user interface of the application therefore should not change too much. The information should flow somewhat continually without much use of side bars or things like that.
https://www.brisk-find.example
Sincerely,
Marco D. Ferral

```html
<!DOCTYPE html>
<html lang="en">
<head>
<meta charset="utf-8">
<title>Brisk Find — Homepage</title>
<link href="https://fonts.googleapis.com/css2?family=Raleway:wght@600;700&family=Roboto:wght@400;500;700&display=swap" rel="stylesheet">
<style>
:root{
  --teal:#3dbdb7;
  --teal-dark:#2fa9a8;
  --teal-light:#4cc9c3;
  --orange:#ee6640;
  --orange-band:#dc5e3b;
  --ink:#111318;
  --body:#5b5f66;
  --grey-card:#f3f3f3;
  --footer:#3b3b3b;
  --white:#ffffff;
}
*{margin:0;padding:0;box-sizing:border-box}
html,body{width:1200px;height:3458px;overflow:hidden}
body{position:relative;background:var(--white);font-family:"Roboto",sans-serif;color:var(--body)}
.abs{position:absolute}
h1,h2,h3.title{font-family:"Raleway",sans-serif;font-weight:700}
.btn{position:absolute;background:var(--orange);color:var(--white);font:700 14px "Roboto",sans-serif;letter-spacing:.4px;display:flex;align-items:center;justify-content:center;border-radius:2px;text-transform:uppercase}

/* hero */
.hero{position:absolute;left:0;top:0;width:1200px;height:621px;background:linear-gradient(160deg,var(--teal-light) 0%,var(--teal) 55%,var(--teal-dark) 100%)}
.brand{position:absolute;left:110px;top:26px;display:flex;align-items:center;gap:8px;font:400 28px "Roboto",sans-serif;color:var(--white)}
.brand-dot{width:30px;height:30px;border-radius:50%;background:var(--white)}
.nav{position:absolute;left:294px;top:38px;display:flex;gap:21px;font:700 13.5px "Roboto",sans-serif;color:var(--white);letter-spacing:.2px}
.login{left:986px;top:24px;width:101px;height:46px;gap:8px}
.hero h1{position:absolute;left:108px;top:248px;width:560px;font-size:40px;line-height:45px;color:var(--white);font-weight:600}
.hero p{position:absolute;left:110px;top:355px;width:540px;font-size:15px;line-height:29px;color:var(--white)}
.hero-btn{left:110px;top:436px;width:154px;height:48px}
.hero-art{left:678px;top:128px;width:456px;height:462px;background:linear-gradient(150deg,#7fe0dc,#2aa7a9);border-radius:14px;opacity:.9}

/* intro */
.intro-art{left:158px;top:714px;width:392px;height:480px;background:linear-gradient(160deg,#bff1ef,#38b8b6 70%,#ef6b45);border-radius:26px}
.intro h2{position:absolute;left:628px;top:720px;width:480px;font-size:38px;line-height:44.5px;color:var(--ink);font-weight:600}
.intro p{position:absolute;left:631px;top:924px;width:470px;font-size:15px;line-height:30px}
.intro-btn{left:631px;top:1127px;width:154px;height:49px}

/* why storage */
.band{position:absolute;left:0;top:1302px;width:1200px;height:648px;background:var(--orange-band)}
.band h2{position:absolute;left:0;top:1368px;width:1200px;text-align:center;font-size:40px;line-height:45px;color:var(--white);font-weight:600}
.tab{position:absolute;top:1492px;height:53px;display:flex;align-items:center;justify-content:center;gap:10px;background:var(--teal);color:var(--white);font:700 14px "Roboto",sans-serif;letter-spacing:.5px;border-radius:2px}
.tab.outline{border:2px solid var(--white)}
.feature{position:absolute;top:1617px;width:230px;text-align:center;color:var(--white)}
.feature .ring{width:86px;height:86px;margin:0 auto;border:3px solid var(--white);border-radius:50%;display:flex;align-items:center;justify-content:center}
.feature h3{margin-top:26px;font:700 14px "Roboto",sans-serif;letter-spacing:.5px}
.feature .rule{width:26px;height:2px;background:var(--white);margin:10px auto 14px}
.feature p{font-size:14.5px;line-height:25px}
.arrow{position:absolute;top:1722px}

/* alternative */
.alt h2{position:absolute;left:123px;top:2106px;width:500px;font-size:38px;line-height:45px;color:var(--ink);font-weight:600}
.alt p{position:absolute;left:126px;top:2213px;width:460px;font-size:15px;line-height:30px}
.alt-btn{left:126px;top:2416px;width:154px;height:49px}
.alt-art{left:700px;top:2049px;width:376px;height:481px;background:linear-gradient(160deg,#bff1ef,#38b8b6 70%,#ef6b45);border-radius:26px}

/* why brisk-find */
.why-title{position:absolute;left:0;top:2634px;width:1200px;text-align:center;font-size:38px;color:var(--ink);font-weight:600}
.card{position:absolute;top:2735px;width:240px;height:251px;padding:30px 24px 0 25px}
.card.shade{background:var(--grey-card)}
.card svg{display:block;height:64px}
.card p{margin-top:26px;font-size:15px;line-height:27.5px}

/* footer */
.footer{position:absolute;left:0;top:3087px;width:1200px;height:371px;background:var(--footer);color:var(--white)}
.footer h4{position:absolute;top:58px;font:700 14px "Roboto",sans-serif;letter-spacing:.3px}
.footer .about{position:absolute;left:111px;top:92px;width:300px;font-size:14.5px;line-height:28.5px}
.links{position:absolute;top:88px;list-style:none;font-size:14.5px;line-height:30px}
.links li::before{content:"»";margin-right:16px}
.news-text{position:absolute;left:808px;top:92px;width:290px;font-size:14.5px;line-height:25px}
.signup{position:absolute;left:809px;top:158px;width:276px;height:43px;border:2px solid var(--white);background:var(--white);display:flex}
.signup span{flex:1;padding-left:14px;display:flex;align-items:center;color:#888;font-size:14px}
.signup b{width:100px;background:var(--orange);display:flex;align-items:center;justify-content:center;font:700 13.5px "Roboto",sans-serif}
.footer .rule{position:absolute;left:111px;top:286px;width:976px;height:1px;background:#6a6a6a}
.copy{position:absolute;left:0;top:316px;width:1200px;text-align:center;font-size:14.5px}
</style>
</head>
<body>

<section class="hero">
  <div class="brand"><span class="brand-dot"></span>Brisk Find</div>
  <nav class="nav"><span>HOME</span><span>ABOUT</span><span>PRICING</span><span>BLOG</span><span>FAQ</span><span>SUPPORT</span><span>REVIEWS</span><span>CONTACT US</span><span>FREE TRIAL</span></nav>
  <div class="btn login">LOG IN
    <svg width="11" height="13" viewBox="0 0 11 13"><path d="M2.5 6V4a3 3 0 0 1 6 0v2" fill="none" stroke="#fff" stroke-width="1.6"/><rect x="1" y="6" width="9" height="7" rx="1" fill="#fff"/></svg>
  </div>
  <h1>Brisk-find along with some best practice techniques</h1>
  <p>Brisk-find is a system that allows you to quickly search for the location of every item that you store or file. It is an essential tool</p>
  <div class="btn hero-btn">30 Day Free Trial</div>
  <div class="abs hero-art" role="img" aria-label="Illustration of a laptop whose screen opens into filing drawers, with a man lifting out a folder"></div>
</section>

<section class="intro">
  <div class="abs intro-art" role="img" aria-label="Illustration of a smartphone with an open drawer and a man carrying a large orange file"></div>
  <h2>Keeping track of all your paper documents &amp; other belongings has never been easier</h2>
  <p>Brisk-find is a system that allows you to quickly search for the location of every item that you store or file. It is an essential tool for keeping track of paper documents. In addition, it is incredibly valuable for storing any other kind of physical items. Giving you the ability to quickly find any item, even years after it has been stored. More importantly, using Brisk-find</p>
  <div class="btn intro-btn">Learn More</div>
</section>

<section class="band"></section>
<h2 class="abs" style="left:0;top:1368px;width:1200px;text-align:center;font-family:'Raleway',sans-serif;font-weight:600;font-size:40px;line-height:45px;color:#fff">Why use a storage management<br>system like Brisk-Find?</h2>
<div class="tab" style="left:255px;width:302px">MANAGING PAPER DOCUMENTS
  <svg width="12" height="14" viewBox="0 0 12 14"><path d="M0 0h8l4 4v10H0z" fill="#fff"/><path d="M3 7h6M3 10h6" stroke="#3dbdb7" stroke-width="1.3"/></svg></div>
<div class="tab outline" style="left:574px;width:371px">MANAGING ANY NON-DOCUMENT OBJECTS
  <svg width="12" height="14" viewBox="0 0 12 14"><path d="M0 0h8l4 4v10H0z" fill="#fff"/><path d="M3 7h6M3 10h6" stroke="#3dbdb7" stroke-width="1.3"/></svg></div>

<svg class="arrow" style="left:45px" width="20" height="34" viewBox="0 0 20 34"><path d="M16 3 4 17l12 14" fill="none" stroke="#fff" stroke-width="3"/></svg>
<svg class="arrow" style="left:1133px" width="20" height="34" viewBox="0 0 20 34"><path d="M4 3l12 14L4 31" fill="none" stroke="#fff" stroke-width="3"/></svg>

<div class="feature" style="left:119px">
  <div class="ring"><svg width="44" height="40" viewBox="0 0 44 40" fill="none" stroke="#fff" stroke-width="2"><path d="M22 6C16 2 8 2 3 4v32c5-2 13-2 19 2 6-4 14-4 19-2V4c-5-2-13-2-19 2zM22 6v32"/><path d="M8 12h9M8 18h9M8 24h9M27 12h9M27 18h9M27 24h9"/></svg></div>
  <h3>BOOKS</h3><div class="rule"></div>
  <p>Whether you keep your books on display on shelves, or stored in boxes, you should keep</p>
</div>
<div class="feature" style="left:363px">
  <div class="ring"><svg width="44" height="44" viewBox="0 0 44 44" fill="none" stroke="#fff" stroke-width="2"><path d="M10 4h6v8l4 6v22H6V18l4-6z"/><path d="M26 12h14c0 8-3 12-7 12s-7-4-7-12zM33 24v14M27 40h12"/></svg></div>
  <h3>WINES</h3><div class="rule"></div>
  <p>Maintaining a constant temperature is essential for good care of quality wines.</p>
</div>
<div class="feature" style="left:607px">
  <div class="ring"><svg width="40" height="44" viewBox="0 0 40 44" fill="none" stroke="#fff" stroke-width="2"><path d="M20 3 5 9v12c0 10 7 17 15 20 8-3 15-10 15-20V9z"/><circle cx="20" cy="22" r="8"/><path d="m16 22 3 3 5-6"/></svg></div>
  <h3>SAFETY BOXES</h3><div class="rule"></div>
  <p>It is common for people to forget exactly which valuables they have stored</p>
</div>
<div class="feature" style="left:851px">
  <div class="ring"><svg width="46" height="40" viewBox="0 0 46 40" fill="none" stroke="#fff" stroke-width="2"><rect x="15" y="10" width="16" height="13"/><circle cx="8" cy="8" r="4"/><circle cx="38" cy="8" r="4"/><path d="M8 12v14l-4 12M8 26l4 12M38 12v14l4 12M38 26l-4 12M8 16h7M38 16h-7"/></svg></div>
  <h3>MOVING BOXES</h3><div class="rule"></div>
  <p>It is always a good idea to record in detail the contents of each box when you move.</p>
</div>

<section class="alt">
  <h2>Alternative uses for Brisk-Find</h2>
  <p>How many times have you gone to a restaurant and couldn’t recall how good (or bad) each of the dishes were that you previously ordered? You can use Brisk-Find to record each one to improve your experience for every visit. Our app can also help you decide where you want to go or which dish to recommend when you have a special occasion</p>
  <div class="btn alt-btn">Learn More</div>
  <div class="abs alt-art" role="img" aria-label="Illustration of a smartphone with an open drawer and a man holding an orange disc case"></div>
</section>

<h2 class="why-title">Why Brisk-Find</h2>

<div class="card" style="left:0">
  <svg width="72" height="64" viewBox="0 0 72 64" fill="none" stroke="#ee6640" stroke-width="2"><path d="M4 50l14-10 10 6 14-12 12 4 14-12"/><circle cx="44" cy="22" r="10"/><path d="M12 10v14M18 16v8M24 12v12"/></svg>
  <p>It is extremely easy to use Lorem ipsum dolor sitamet, consectetur adipiscing elit, sed do eiusmod tempor</p>
</div>
<div class="card shade" style="left:240px">
  <svg width="50" height="66" viewBox="0 0 50 66" fill="none" stroke="#3dbdb7" stroke-width="2"><rect x="4" y="2" width="42" height="62"/><path d="M10 10h14M10 22h8v8h-8zM10 40h8v8h-8zM24 26h16M24 44h16" stroke="#ee6640"/></svg>
  <p>It Adapts to your stile. Since each catalog can have 1 or more levels of depth (folders and sub-folders), Brisk-Find</p>
</div>
<div class="card" style="left:480px">
  <svg width="60" height="64" viewBox="0 0 60 64" fill="none" stroke="#ee6640" stroke-width="2"><path d="M4 54l14-12h14l18-14"/><circle cx="32" cy="34" r="10"/><path d="M40 12h14v10H40z" stroke="#3dbdb7"/></svg>
  <p>It’s very affordable. Checkout our pricing plans! It’s very affordable. Checkout our pricing plans!</p>
</div>
<div class="card shade" style="left:720px">
  <svg width="60" height="64" viewBox="0 0 60 64" fill="none" stroke="#ee6640" stroke-width="2"><rect x="4" y="24" width="40" height="30"/><circle cx="24" cy="36" r="6"/><path d="M14 54c0-7 5-10 10-10s10 3 10 10"/><rect x="38" y="6" width="18" height="12" stroke="#3dbdb7"/></svg>
  <p>Since it is online, your data is available almost anywhere in the world.</p>
</div>
<div class="card" style="left:960px">
  <svg width="66" height="64" viewBox="0 0 66 64" fill="none" stroke="#ee6640" stroke-width="2"><rect x="4" y="4" width="50" height="40" stroke="#3dbdb7"/><path d="M14 36V26M22 36V18M30 36V24"/><circle cx="42" cy="42" r="10"/><path d="M49 49l10 10"/></svg>
  <p>Data encryption ensures that your information is always private, safe, and secure</p>
</div>

<footer class="footer">
  <h4 style="left:111px">ABOUT US</h4>
  <p class="about">Laboratory samples frequently need to be stored at constant cold temperatures. Our system was originally designed to fulfill the needs of a laboratory which needed an efficient way to minimize</p>
  <h4 style="left:444px">QUICK LINKS</h4>
  <ul class="links" style="left:444px"><li>Home</li><li>About Us</li><li>Pricing</li><li>Blog</li><li>Support</li></ul>
  <h4 style="left:641px">QUICK LINKS</h4>
  <ul class="links" style="left:641px"><li>FAQ</li><li>Free Trial</li><li>Services</li><li>Reviews</li><li>Contact Us</li></ul>
  <h4 style="left:804px">NEWSLETTER</h4>
  <p class="news-text">Lorem ipsum dolor sit amet, consectetur adipiscing elit, sed do eiusmod tempor</p>
  <div class="signup"><span>Email</span><b>SUBSCRIBE</b></div>
  <div class="rule"></div>
  <p class="copy">© 2021 Brisk Find. All Rights Reserved</p>
</footer>

</body>
</html>
```